UI/ UX Design for ERP Software

We need a new UX/UI interface for a ERP software for property managers. Our CMMS / ERP solution is made based on responsive design technologies and is coded in PHP.
The overall UX to be similar to Tev Ulna - easy navigation, intuitive menus.

Industry/Entity Type

Property Management

Number of Pages Required

5+ page

Requirements
Must have
• Round dock buttons
Consistent icons across the application
Enough Spacing between buttons/icons/ menu
Consistent Font
Nice to have
• We would like the UX to allow the users to use the application without /minimum training.
Should not have
• we don't want anything that is classic with respect to UX

```html
<!DOCTYPE html>
<html lang="en">
<head>
<meta charset="utf-8">
<title>Lotwise – Active Dashboard</title>
<link href="https://fonts.googleapis.com/css2?family=Mulish:wght@400;600;700;800&display=swap" rel="stylesheet">
<style>
  :root {
    --bg-top: #556680;
    --bg-bottom: #4b5a70;
    --pill: #2f3a4b;
    --round-btn: #5a6a82;
    --white: #ffffff;
    --tab: #00b6f7;
    --tab-active-a: #0a9ef5;
    --tab-active-b: #0066f5;
    --ink: #4a5670;
    --axis-label: #2f3a4b;
    --cyan: #00b4f0;
    --bar: #0077fb;
    --bar-track: #efefef;
    --c-blue: #0a73f5;
    --c-green: #8ee87a;
    --c-orange: #f6a05a;
    --c-dark: #3e3f47;
    --c-violet: #8083e6;
    --c-pink: #ef5b7e;
    --c-yellow: #e6d654;
  }
  * { box-sizing: border-box; margin: 0; padding: 0; }
  html, body { width: 1200px; height: 857px; overflow: hidden; }
  body {
    font-family: "Mulish", sans-serif;
    background: linear-gradient(180deg, var(--bg-top), var(--bg-bottom));
    position: relative;
    color: var(--white);
  }
  .brand {
    position: absolute; left: 88px; top: 26px;
    display: flex; align-items: center; gap: 7px;
    font-weight: 800; font-size: 21px; color: var(--white);
  }
  .brand-mark { width: 14px; height: 14px; background: var(--white); border-radius: 50%; }

  .stat {
    position: absolute; top: 20px; height: 38px;
    background: var(--pill); border-radius: 19px;
    display: flex; align-items: center; gap: 10px; padding-left: 12px;
    font-size: 11px; line-height: 13px; color: #e4e9f1;
  }
  .stat svg { width: 20px; height: 20px; flex: none; }

  .round-btn {
    position: absolute; top: 94px; width: 40px; height: 40px; border-radius: 50%;
    background: var(--round-btn); display: flex; align-items: center; justify-content: center;
  }
  .page-title {
    position: absolute; left: 155px; top: 95px;
    font-size: 28px; font-weight: 700; letter-spacing: 0.3px;
  }

  .card {
    position: absolute; left: 80px; top: 161px; width: 1040px; height: 619px;
    background: var(--white); border-radius: 40px; overflow: hidden;
  }
  .tabs { position: absolute; left: 351px; top: 0; display: flex; gap: 2px; }
  .tab {
    width: 107px; height: 41px; background: var(--tab);
    display: flex; align-items: center; justify-content: center; gap: 4px;
    font-size: 9px; font-weight: 800; letter-spacing: 0.2px; color: var(--white);
  }
  .tab.is-active { background: linear-gradient(180deg, var(--tab-active-a), var(--tab-active-b)); }
  .tab svg { width: 8px; height: 8px; }

  .range {
    position: absolute; left: 53px; top: 57px;
    font-size: 23px; font-weight: 700; letter-spacing: 1.5px; color: var(--ink);
    word-spacing: 6px;
  }
  .chart { position: absolute; left: 0; top: 0; }
  .chart text { font-family: "Mulish", sans-serif; }

  .legend { position: absolute; left: 65px; top: 526px; width: 960px; }
  .legend-item {
    position: absolute; display: flex; align-items: center; gap: 5px;
    font-size: 9.5px; line-height: 11px; color: var(--ink); letter-spacing: 0.3px;
  }
  .dot { width: 28px; height: 28px; border-radius: 50%; flex: none; }
</style>
</head>
<body>
  <div class="brand"><span class="brand-mark"></span>Lotwise</div>

  <div class="stat" style="left:460px;width:103px">
    <svg viewBox="0 0 20 20" fill="none" stroke="#c9d2de" stroke-width="1.2"><path d="M3 10 L10 3.5 L17 10 M5 8.5 V17 H8.5 V12.5 H11.5 V17 H15 V8.5"/></svg>
    <div>Properties<br>3</div>
  </div>
  <div class="stat" style="left:572px;width:103px">
    <svg viewBox="0 0 20 20" fill="none" stroke="#c9d2de" stroke-width="1.1"><circle cx="10" cy="6.5" r="2.5"/><circle cx="4.5" cy="8" r="1.8"/><circle cx="15.5" cy="8" r="1.8"/><path d="M5.5 15 a4.5 4.5 0 0 1 9 0 M1 15 a3.5 3.5 0 0 1 4.5-3.3 M19 15 a3.5 3.5 0 0 0 -4.5-3.3"/></svg>
    <div>Tenants<br>8</div>
  </div>
  <div class="stat" style="left:685px;width:152px">
    <svg viewBox="0 0 20 20" fill="none" stroke="#c9d2de" stroke-width="1"><circle cx="10" cy="10" r="8.5" stroke-dasharray="3 1.5"/><circle cx="10" cy="10" r="3.5"/><path d="M10 4 V16 M4 10 H16"/></svg>
    <div>Total Properties area<br>422,000.00Sq.ft</div>
  </div>
  <div class="stat" style="left:847px;width:130px">
    <svg viewBox="0 0 20 20" fill="none" stroke="#c9d2de" stroke-width="1"><circle cx="10" cy="10" r="8.5" stroke-dasharray="3 1.5"/><circle cx="10" cy="10" r="3.5"/><path d="M10 4 V16 M4 10 H16"/></svg>
    <div>Rented area<br>233,500.00sq.ft</div>
  </div>
  <div class="stat" style="left:988px;width:130px">
    <svg viewBox="0 0 20 20" fill="none" stroke="#c9d2de" stroke-width="1"><circle cx="10" cy="10" r="8.5" stroke-dasharray="3 1.5"/><circle cx="10" cy="10" r="3.5"/><path d="M10 4 V16 M4 10 H16"/></svg>
    <div>Vacancies area<br>188,500.00sq.ft</div>
  </div>

  <div class="round-btn" style="left:100px">
    <svg width="14" height="12" viewBox="0 0 14 12" fill="#fff"><path d="M7 0 L14 6 H12 V12 H8.5 V8 H5.5 V12 H2 V6 H0 Z"/></svg>
  </div>
  <h1 class="page-title">Active Dashboard</h1>
  <div class="round-btn" style="left:1075px">
    <svg width="14" height="12" viewBox="0 0 14 12" fill="#fff"><rect y="0" width="14" height="2.2"/><rect y="4.9" width="14" height="2.2"/><rect y="9.8" width="14" height="2.2"/></svg>
  </div>

  <main class="card">
    <nav class="tabs">
      <div class="tab is-active"><svg viewBox="0 0 8 8" fill="none" stroke="#fff" stroke-width="1.2"><circle cx="4" cy="4" r="3.3"/><path d="M4 2 V4 H5.5"/></svg>LAST 7 DAYS</div>
      <div class="tab"><svg viewBox="0 0 8 8" fill="none" stroke="#fff" stroke-width="1.2"><circle cx="4" cy="4" r="3.3"/><path d="M4 2 V4 H5.5"/></svg>LAST MONTHS</div>
      <div class="tab"><svg viewBox="0 0 8 8" fill="none" stroke="#fff" stroke-width="1.2"><circle cx="4" cy="4" r="3.3"/><path d="M4 2 V4 H5.5"/></svg>LAST 3 MONTHS</div>
      <div class="tab"><svg viewBox="0 0 8 8" fill="none" stroke="#fff" stroke-width="1.2"><circle cx="4" cy="4" r="3.3"/><path d="M4 2 V4 H5.5"/></svg>NEXT 7 DAYS</div>
      <div class="tab"><svg viewBox="0 0 8 8" fill="none" stroke="#fff" stroke-width="1.2"><circle cx="4" cy="4" r="3.3"/><path d="M4 2 V4 H5.5"/></svg>NEXT MONTHS</div>
      <div class="tab"><svg viewBox="0 0 8 8" fill="none" stroke="#fff" stroke-width="1.2"><circle cx="4" cy="4" r="3.3"/><path d="M4 2 V4 H5.5"/></svg>NEXT 3 MONTHS</div>
    </nav>

    <div class="range">12/27/2020 - 01/03/2021</div>

    <svg class="chart" width="1040" height="520" viewBox="0 0 1040 520">
      <text x="28" y="300" transform="rotate(-90 28 300)" fill="var(--cyan)" font-size="9" font-weight="600" letter-spacing="0.5" text-anchor="middle">NUMBER</text>
      <g fill="var(--axis-label)" font-size="9" font-weight="600">
        <text x="53" y="156">1.25</text>
        <text x="53" y="214">1</text>
        <text x="53" y="273">0.75</text>
        <text x="53" y="332">0.5</text>
        <text x="53" y="390">0.25</text>
        <text x="53" y="449">0</text>
      </g>
      <line x1="83" y1="449.5" x2="998" y2="449.5" stroke="#dcdfe4" stroke-width="1"/>
      <rect x="450" y="141" width="14" height="308" rx="7" fill="var(--bar-track)"/>
      <path d="M450 449 V202 a7 7 0 0 1 14 0 V449 Z" fill="var(--bar)"/>
      <g fill="var(--axis-label)" font-size="9" font-weight="600" letter-spacing="0.4" text-anchor="middle">
        <text x="113" y="481">12/27/2020</text>
        <text x="236" y="481">12/28/2020</text>
        <text x="359" y="481">12/29/2020</text>
        <text x="482" y="481">12/30/2020</text>
        <text x="605" y="481">12/31/2020</text>
        <text x="728" y="481">01/01/2021</text>
        <text x="851" y="481">01/02/2021</text>
        <text x="974" y="481">01/03/2021</text>
      </g>
    </svg>

    <div class="legend">
      <div class="legend-item" style="left:0;top:4px"><span class="dot" style="background:var(--c-blue)"></span>Sheduled<br>Maintenance</div>
      <div class="legend-item" style="left:143px;top:4px"><span class="dot" style="background:var(--c-green)"></span>Completed<br>Sheduled<br>Maintenance</div>
      <div class="legend-item" style="left:278px;top:4px"><span class="dot" style="background:var(--c-orange)"></span>Future Sheduled<br>Maintenance</div>
      <div class="legend-item" style="left:420px;top:4px"><span class="dot" style="background:var(--c-dark)"></span>Sheduled Work<br>Orders</div>
      <div class="legend-item" style="left:568px;top:4px"><span class="dot" style="background:var(--c-violet)"></span>Completed<br>Work Orders</div>
      <div class="legend-item" style="left:708px;top:4px"><span class="dot" style="background:var(--c-pink)"></span>Property<br>Inspections in<br>Progress</div>
      <div class="legend-item" style="left:855px;top:4px"><span class="dot" style="background:var(--c-yellow)"></span>Completed<br>Property<br>Inspections</div>
    </div>
  </main>
</body>
</html>
```